Personalized Technology Company Needs a Business Card

I need a double-sided business card. Both sides will have the logo, and the contact information. One side will be black, with the white / gray logo, and the other will be white, with the black / gray logo. The black side will have the text "Custom Gaming PC's" and will have a water-cooled gaming PC image. The white side will have the text "Custom Business Computers & Consulting", and will have a business / enterprise PC image. Feel free to add a conservative image in the background, while the color remains unchanged. I'm uploading the base logo (transparent), so you can modify the colors, both the finished colored logos and an idea of ​​the business card (with the current information, just missing the website, which is www.velomindsystems.com, please add it.) Thank you so much for your effort, I'll be specting your cool designs. Good Luck!

Target Market(s)

Gamers & Entrepreneurs / Business Owners / Chief Technology Officers

Industry/Entity Type

Technology Equipment

Contact Information for Business Card

I need a double-sided business card. Both sides will have the logo, and the contact information. One side will be black, with the white/gray logo, and the other one will be white, with the black/gray logo. The black side will have the text "Custom Gaming PC's" and will have a water-cooled gaming PC image. The white side will have the text "Custom Business Computers & Consulting", and will have a business/enterprise PC image. Feel free to add a conservative image in the background, whilst the color remains unchanged.

I'm uploading the base logo (transparent), so you can modify the colors, both the finished colored logos and an idea of the business card (with the actual information, just missing the website, which is www.velomindsystems.com, please add it.)

Thank you so much for your effort, I'll be specting your cool designs. Good Luck!

Font styles to use
Serif

Colors
000000
757575
ffffff

Requirements
Must have
• Please See Description
Nice to have
• Please See Description
Should not have
• Please See Description

```html
<!DOCTYPE html>
<html lang="en">
<head>
<meta charset="utf-8">
<title>Velomind Systems Business Card</title>
<link rel="stylesheet" href="https://fonts.googleapis.com/css2?family=Tinos:wght@400;700&display=swap">
<style>
  :root {
    --ink: #000000;
    --grey: #757575;
    --paper: #ffffff;
    --stage: #1d1d20;
    --sand: #e4dcd0;
    --sand-dark: #b9ab98;
    --photo-deep: #0c1a4a;
    --photo-mid: #2350b8;
    --photo-light: #5fc8f0;
  }
  * { box-sizing: border-box; margin: 0; padding: 0; }
  html, body { width: 1200px; height: 800px; overflow: hidden; }
  body {
    background: var(--stage);
    font-family: "Tinos", "Times New Roman", serif;
    display: flex; align-items: center; justify-content: center; gap: 40px;
  }
  .card {
    position: relative; width: 560px; height: 320px; overflow: hidden;
    box-shadow: 0 12px 30px rgba(0,0,0,.5);
  }
  .card--dark { background: var(--ink); color: var(--paper); }
  .card--light { background: var(--paper); color: var(--ink); }
  .card__art { position: absolute; inset: 0; }
  .brand {
    position: absolute; left: 34px; top: 150px;
    display: flex; align-items: center; gap: 12px;
  }
  .brand__dot { width: 26px; height: 26px; border-radius: 50%; background: var(--grey); }
  .brand__name { font-size: 30px; font-weight: 700; letter-spacing: 2px; line-height: 1; }
  .person { position: absolute; left: 34px; top: 196px; }
  .person__name { font-size: 17px; font-weight: 700; }
  .person__role { font-size: 12px; color: #cfcfcf; }
  .contacts { position: absolute; left: 34px; top: 238px; width: 240px; font-size: 11px; line-height: 1.4; }
  .contacts__row { display: flex; align-items: center; gap: 8px; padding: 3px 0; }
  .contacts__row + .contacts__row { border-top: 1px dotted #bdbdbd; }
  .contacts__icon { width: 14px; height: 14px; flex: none; }
  .tagline {
    position: absolute; text-transform: uppercase; text-align: center;
    font-size: 13px; letter-spacing: .5px; line-height: 1.3;
  }
  .tagline--gaming {
    right: 26px; bottom: 34px; padding: 7px 16px;
    border: 2px solid #9a9a9a; border-radius: 6px; color: var(--paper);
  }
  .tagline--business {
    right: 26px; top: 202px; padding: 10px 16px;
    border: 4px double var(--sand-dark); color: var(--ink);
  }
  .social { position: absolute; left: 34px; bottom: 26px; display: flex; align-items: center; gap: 7px; font-size: 12px; }
  .social__dot { width: 14px; height: 14px; border-radius: 50%; background: var(--ink); }
  .social__url { margin-left: 6px; }
</style>
</head>
<body>

<section class="card card--dark">
  <svg class="card__art" viewBox="0 0 560 320">
    <defs>
      <linearGradient id="gaming-photo" x1="0" y1="1" x2="1" y2="0">
        <stop offset="0" stop-color="var(--photo-deep)"/>
        <stop offset=".55" stop-color="var(--photo-mid)"/>
        <stop offset="1" stop-color="var(--photo-light)"/>
      </linearGradient>
    </defs>
    <path d="M185 0 Q290 182 560 128 L560 0 Z" fill="var(--sand)"/>
    <path role="img" aria-label="Photo of a water-cooled custom gaming PC interior lit in blue" d="M196 0 Q295 168 560 118 L560 0 Z" fill="url(#gaming-photo)"/>
  </svg>
  <div class="brand"><span class="brand__dot"></span><span class="brand__name">VELOMIND SYSTEMS</span></div>
  <div class="person">
    <div class="person__name">Marco Ruiz Delano</div>
    <div class="person__role">(CEO &amp; Co-Founder)</div>
  </div>
  <div class="contacts">
    <div class="contacts__row">
      <svg class="contacts__icon" viewBox="0 0 14 14"><path d="M3 1h3l1 3-2 1a7 7 0 0 0 4 4l1-2 3 1v3c0 1-1 2-2 2A11 11 0 0 1 1 3c0-1 1-2 2-2z" fill="#fff"/></svg>
      <span>+52 5100 - 2840 &nbsp;·&nbsp; +52 55 - 4180 - 3316</span>
    </div>
    <div class="contacts__row">
      <svg class="contacts__icon" viewBox="0 0 14 14"><circle cx="7" cy="7" r="5.5" fill="none" stroke="#fff" stroke-width="1.2"/><path d="M1.5 7h11M7 1.5c-3 3-3 8 0 11M7 1.5c3 3 3 8 0 11" fill="none" stroke="#fff" stroke-width="1"/></svg>
      <span>contact@velomindsystems.com<br>www.velomindsystems.com</span>
    </div>
  </div>
  <div class="tagline tagline--gaming">Custom Gaming PC's</div>
</section>

<section class="card card--light">
  <svg class="card__art" viewBox="0 0 560 320">
    <defs>
      <linearGradient id="business-photo" x1="0" y1="1" x2="1" y2="0">
        <stop offset="0" stop-color="#0d2a66"/>
        <stop offset=".5" stop-color="#1f6fc8"/>
        <stop offset="1" stop-color="#7fe0ff"/>
      </linearGradient>
    </defs>
    <path d="M205 0 Q300 178 560 124 L560 0 Z" fill="var(--sand)"/>
    <path role="img" aria-label="Photo of a business workstation with glowing blue panels" d="M216 0 Q305 164 560 114 L560 0 Z" fill="url(#business-photo)"/>
  </svg>
  <div class="brand"><span class="brand__dot"></span><span class="brand__name">VELOMIND SYSTEMS</span></div>
  <div class="tagline tagline--business">Custom Business<br>Computers &amp; Consulting</div>
  <div class="social">
    <span class="social__dot"></span><span class="social__dot"></span><span class="social__dot"></span>
    <span class="social__url">www.velomindsystems.com</span>
  </div>
</section>

</body>
</html>
```